A clean crisp business card for a Landscape Construction company. Designed to be easy to read contact/ info and also be appealing/interesting, unlike a traditional business card.

Industry/Entity Type

Landscape Construction

Contact Information for Business Card

Company name : Brambleford Landscape Construction, phone number: (877) 62Vista, website:Bramblefordyards.example, Email, sales@bramblefordyards.example

Requirements
Nice to have
• Luxurious finishes/ details…. Icons or emblems next to contact info
Should not have
• Clipart or general pictures

```html
<!DOCTYPE html>
<html lang="en">
<head>
<meta charset="utf-8">
<title>Brambleford Landscape Construction – Business Card</title>
<link rel="stylesheet" href="https://fonts.googleapis.com/css2?family=Fira+Sans+Condensed:wght@300;400;600&display=swap">
<style>
  :root {
    --backdrop: #2b2b2d;
    --card: #141416;
    --card-edge: #1d1d20;
    --blue: #1b7fd8;
    --green: #a9cc2c;
    --ink-light: #c9cbcf;
    --silver: #b9bcc2;
  }
  * { box-sizing: border-box; margin: 0; padding: 0; }
  html, body { width: 1200px; height: 874px; overflow: hidden; }
  body {
    background: var(--backdrop);
    font-family: "Fira Sans Condensed", "Arial Narrow", sans-serif;
    position: relative;
  }
  .card {
    position: absolute;
    left: 320px;
    width: 560px;
    height: 320px;
    background: var(--card);
    border: 1px solid var(--card-edge);
    border-radius: 18px;
    box-shadow: 0 18px 40px rgba(0,0,0,.55);
    overflow: hidden;
  }
  .card--back { top: 60px; }
  .card--front { top: 430px; }

  /* back side */
  .back-mark {
    position: absolute;
    top: 96px; left: 0; right: 0;
    display: flex; align-items: center; justify-content: center; gap: 14px;
  }
  .back-mark__dot {
    width: 22px; height: 22px; border-radius: 50%;
    background: var(--silver);
  }
  .back-mark__name {
    font-size: 46px; font-weight: 400; letter-spacing: 3px;
    color: var(--silver); text-transform: uppercase;
  }
  .back-url {
    position: absolute; top: 232px; left: 0; right: 0; text-align: center;
    font-size: 17px; letter-spacing: 1.5px; text-transform: uppercase;
    color: var(--blue);
  }
  .back-url strong { color: var(--green); font-weight: 600; }

  /* front side */
  .brand {
    position: absolute; left: 40px; top: 128px;
    display: flex; align-items: center; gap: 10px;
  }
  .brand__dot { width: 14px; height: 14px; border-radius: 50%; background: var(--blue); }
  .brand__name {
    font-size: 21px; font-weight: 400; line-height: 1.15;
    color: var(--blue); text-transform: uppercase; letter-spacing: 1px;
  }
  .person { position: absolute; left: 318px; top: 92px; }
  .person__name {
    font-size: 27px; font-weight: 600; color: var(--blue);
    text-transform: uppercase; letter-spacing: .5px;
  }
  .person__title {
    font-size: 14px; color: var(--green); text-transform: uppercase; margin-top: 1px;
  }
  .person__rule { width: 26px; height: 2px; background: var(--blue); margin: 10px 0 14px; }
  .contact { list-style: none; }
  .contact li {
    display: flex; align-items: center; gap: 8px;
    font-size: 13.5px; font-weight: 300; color: var(--ink-light);
    text-transform: uppercase; line-height: 1.55;
  }
  .contact svg { width: 11px; height: 11px; fill: var(--green); flex: none; }
</style>
</head>
<body>

<section class="card card--back" aria-label="Card back">
  <div class="back-mark">
    <span class="back-mark__dot"></span>
    <span class="back-mark__name">Brambleford</span>
  </div>
  <p class="back-url">www.<strong>bramblefordyards</strong>.example</p>
</section>

<section class="card card--front" aria-label="Card front">
  <div class="brand">
    <span class="brand__dot"></span>
    <span class="brand__name">Brambleford<br>Landscape Construction</span>
  </div>

  <div class="person">
    <h1 class="person__name">Owen Caldwell</h1>
    <p class="person__title">President</p>
    <div class="person__rule"></div>
    <ul class="contact">
      <li>
        <svg viewBox="0 0 24 24" aria-hidden="true"><path d="M6.6 10.8a15.1 15.1 0 0 0 6.6 6.6l2.2-2.2a1 1 0 0 1 1-.25 11.4 11.4 0 0 0 3.6.57 1 1 0 0 1 1 1V20a1 1 0 0 1-1 1A17 17 0 0 1 3 4a1 1 0 0 1 1-1h3.5a1 1 0 0 1 1 1c0 1.25.2 2.45.57 3.57a1 1 0 0 1-.25 1z"/></svg>
        (877) 62Vista
      </li>
      <li>
        <svg viewBox="0 0 24 24" aria-hidden="true"><path d="M2 5h20v14H2z M3 6l9 7 9-7" stroke="#141416" stroke-width="1.5"/></svg>
        sales@bramblefordyards.example
      </li>
      <li>
        <svg viewBox="0 0 24 24" aria-hidden="true"><circle cx="12" cy="12" r="10"/><path d="M2 12h20M12 2c3 3 3 17 0 20M12 2c-3 3-3 17 0 20" stroke="#141416" stroke-width="1.5" fill="none"/></svg>
        Bramblefordyards.example
      </li>
    </ul>
  </div>
</section>

</body>
</html>
```